Elegant Business Card for Technology Company

Client is a supplier of innovative industrial communications and automation equipment since 2002. This contest is to gather fresh ideas for a redesign of the existing business card. Client is looking for design that best communicates tagline "Industrial Networking and Computing Specialist".

Design submissions should look modern, clean, elegant and professional. It should not be cluttered. Use white as the primary colour. Orange and black as secondary colour. Refer to jpeg File 1 on the current design.

Fonts used by Client used include Arial Regular, Arial Black, Roboto Regular, Roboto Black and Lato.

The winning design will be sent for offset printing using super white 250gsm artcard paper (open for suggestions).

Target Market(s)

System Engineers, Project Managers, Purchasing Managers from companies providing engineering services for Smart Cities.

Industry/Entity Type

Information Technology

Contact Information for Business Card

Refer to PDF File 3 for Business Card Details. Priority of short contact information would be as follows Name > Job Title > Email > Mobile > Web > Tel > Fax > Business Address >UEN (UEN represents company registration number)

Font styles to use
Sans Serif

Colors
ffffff
f37122
000000
5c5c5c

Requirements
Must have
• Refer to AI File 2 (Company Logo) & PDF File 3 (Information on Namecard)
Should not have
• No QR codes
• No Social Media Icons
• Do not create full Black or Orange colour background

```html
<!DOCTYPE html>
<html lang="en">
<head>
<meta charset="utf-8">
<title>Korvex Asia Pacific – Business Card</title>
<link rel="stylesheet" href="https://fonts.googleapis.com/css2?family=Lato:wght@400;700;900&display=swap">
<style>
  :root{
    --white:#ffffff;
    --orange:#f37122;
    --black:#000000;
    --grey:#5c5c5c;
    --stage:#e9e7e3;
    --card-shadow:0 14px 30px rgba(0,0,0,.18);
  }
  *{box-sizing:border-box;margin:0;padding:0}
  html,body{width:1200px;height:780px;overflow:hidden}
  body{background:var(--stage);font-family:"Lato",sans-serif;color:var(--black);position:relative}
  .card{position:absolute;top:235px;width:540px;height:310px;background:linear-gradient(135deg,#ffffff 0%,#f4f4f4 100%);border-radius:16px;box-shadow:var(--card-shadow);overflow:hidden}
  .card--front{left:40px}
  .card--back{left:620px}

  /* brand mark */
  .brand{display:flex;align-items:center;gap:8px}
  .brand__dot{width:46px;height:46px;border-radius:50%;background:var(--orange);flex:none}
  .brand__name{font-weight:900;font-size:34px;letter-spacing:1px;color:var(--black)}

  /* front */
  .front__web{position:absolute;top:26px;right:34px;color:var(--orange);font-size:14px}
  .front__brand{position:absolute;left:34px;top:92px}
  .front__company{position:absolute;left:34px;top:150px;font-size:17px;color:var(--black)}
  .front__person{position:absolute;right:34px;top:82px;text-align:right}
  .person__name{font-size:25px;font-weight:700;letter-spacing:-.3px}
  .person__title{font-size:14px;color:var(--orange);margin-top:1px}
  .front__rule{position:absolute;left:34px;right:34px;top:188px;height:1px;background:var(--orange);opacity:.8}
  .front__contacts{position:absolute;left:34px;bottom:24px;list-style:none;font-size:13.5px;line-height:20px;color:var(--black)}
  .front__contacts li{display:flex;align-items:center;gap:8px}
  .icon{width:15px;height:15px;flex:none}
  .front__address{position:absolute;right:34px;bottom:24px;text-align:right;font-size:13.5px;line-height:20px}
  .front__uen span{color:var(--orange)}

  /* back */
  .back__brand{position:absolute;right:34px;top:26px}
  .back__tagline{position:absolute;left:34px;top:96px;font-size:16px;color:var(--black)}
  .back__services{position:absolute;left:34px;top:124px;list-style:none;font-size:13.5px;line-height:20px}
  .back__services li{display:flex;align-items:center;gap:9px}
  .back__services li::before{content:"";width:7px;height:7px;border-radius:50%;background:var(--orange);flex:none}
  .back__web{position:absolute;left:34px;top:232px;color:var(--orange);font-size:13.5px}
  .back__texture{position:absolute;left:0;bottom:0;width:300px;height:120px;background:radial-gradient(ellipse at 20% 100%,rgba(243,113,34,.10),rgba(243,113,34,0) 70%)}
  .back__company{position:absolute;right:34px;bottom:26px;font-size:15px}
  .back__tiles{position:absolute;left:34px;bottom:22px;display:flex;gap:8px}
  .back__tiles span{width:18px;height:18px;border-radius:3px;background:#d9d9d9}
</style>
</head>
<body>

<section class="card card--front" aria-label="Business card front">
  <a class="front__web">www.korvex.com</a>
  <div class="brand front__brand"><span class="brand__dot"></span><span class="brand__name">KORVEX</span></div>
  <p class="front__company">Korvex Asia Pacific Pte Ltd</p>
  <div class="front__person">
    <p class="person__name">Daniel Ong</p>
    <p class="person__title">Sales Manager</p>
  </div>
  <div class="front__rule"></div>
  <ul class="front__contacts">
    <li><svg class="icon" viewBox="0 0 15 15"><rect width="15" height="15" rx="2" fill="#f37122"/><rect x="5" y="3" width="5" height="9" rx="1" fill="none" stroke="#fff" stroke-width="1.2"/></svg>+65 8123 4567</li>
    <li><svg class="icon" viewBox="0 0 15 15"><rect width="15" height="15" rx="2" fill="#f37122"/><path d="M4 4c0 4 3 7 7 7l1-2-2-1-1 1c-1-.5-2-1.5-2.5-2.5l1-1-1-2z" fill="#fff"/></svg>+65 6555 2140</li>
    <li><svg class="icon" viewBox="0 0 15 15"><rect width="15" height="15" rx="2" fill="#f37122"/><rect x="3.5" y="6" width="8" height="5" fill="none" stroke="#fff" stroke-width="1.2"/><rect x="5" y="3.5" width="5" height="2.5" fill="#fff"/></svg>+65 6555 2183</li>
    <li><svg class="icon" viewBox="0 0 15 15"><rect width="15" height="15" rx="2" fill="#f37122"/><rect x="3" y="4.5" width="9" height="6" fill="none" stroke="#fff" stroke-width="1.2"/><path d="M3 4.5l4.5 3.5 4.5-3.5" fill="none" stroke="#fff" stroke-width="1.2"/></svg>sales@korvex.com.sg</li>
  </ul>
  <div class="front__address">
    <p class="front__uen"><span>UEN No</span> 200305117</p>
    <p>22 Kallen Crescent Kallen Techpark</p>
    <p>#04-12 (Lobby B), Singapore 417903</p>
  </div>
</section>

<section class="card card--back" aria-label="Business card back">
  <div class="back__texture" role="img" aria-label="Faint orange dot texture"></div>
  <div class="brand back__brand"><span class="brand__dot"></span><span class="brand__name">KORVEX</span></div>
  <p class="back__tagline">Industrial Networking and Computing Specialist</p>
  <ul class="back__services">
    <li>Industrial Ethernet / Wireless / Cellular</li>
    <li>Industrial and Emedded Computing</li>
    <li>Serial / Fieldbus Connectivity</li>
    <li>IP Video Surveillance</li>
    <li>Remote Automation</li>
  </ul>
  <a class="back__web">www.korvex.com</a>
  <div class="back__tiles" aria-hidden="true"><span></span><span></span><span></span></div>
  <p class="back__company">Korvex Asia Pacific Pte Ltd</p>
</section>

</body>
</html>
```